Irrigation Business needs their business cards modernised and revamped

I would like to keep my current logo, colours and revamp the format of the card.

I would like the card to be clean yet important.

Im not sure if you include texture but i would like the named logo to be indented into the card etc.

show me something alive and free something thats clinical to the point yet has a feel of achievement. i would like people to go nice card.

Target Market(s)

high end clients, corporate, sports field manger, the guys that make the decisions

Industry/Entity Type

Business

Contact Information for Business Card

nformation to be included

Dean Harlow (Director)
0487305526
dean@kolvat.biz
www.kestonfieldworks.com

instagram logo
google logo
facebook logo

Colors

Designer to choose colors to be used in the design.

Requirements
Nice to have
• indentations a really nice feel to the card good texture

```html
<!DOCTYPE html>
<html lang="en">
<head>
<meta charset="utf-8">
<title>Keston Fieldworks – Business Card</title>
<link rel="stylesheet" href="https://fonts.googleapis.com/css2?family=Open+Sans:wght@400;600;700&display=swap">
<style>
  :root {
    --backdrop: #3b302b;
    --card: #141516;
    --card-edge: #1d1f21;
    --brand-blue: #2f86c0;
    --mark-teal: #2e8aa8;
    --accent-green: #2fa84f;
    --text-light: #f2f2f2;
    --divider: #6d7378;
    --social: #24506f;
  }
  * { box-sizing: border-box; margin: 0; padding: 0; }
  html, body { width: 1200px; height: 864px; overflow: hidden; }
  body {
    background: var(--backdrop);
    font-family: "Open Sans", Arial, sans-serif;
    display: flex;
    align-items: center;
    justify-content: center;
    gap: 48px;
  }
  .card {
    width: 540px;
    height: 300px;
    background: var(--card);
    border: 1px solid var(--card-edge);
    box-shadow: 0 14px 30px rgba(0,0,0,.45);
    position: relative;
  }

  /* Back of card */
  .card-back {
    display: flex;
    flex-direction: column;
    align-items: center;
    justify-content: center;
    gap: 18px;
  }
  .brand-disc {
    width: 120px; height: 120px;
    border-radius: 50%;
    background: var(--mark-teal);
  }
  .brand-name-large {
    font-weight: 700;
    font-size: 20px;
    letter-spacing: 1px;
    text-transform: uppercase;
    color: var(--brand-blue);
  }
  .social-row { display: flex; gap: 8px; }
  .social-dot {
    width: 16px; height: 16px;
    border-radius: 50%;
    background: var(--social);
  }

  /* Front of card */
  .card-front {
    display: flex;
    align-items: center;
  }
  .brand-block {
    width: 270px;
    display: flex;
    flex-direction: column;
    align-items: center;
    gap: 10px;
  }
  .brand-dot {
    width: 48px; height: 48px;
    border-radius: 50%;
    background: var(--mark-teal);
  }
  .brand-name {
    font-weight: 700;
    font-size: 19px;
    letter-spacing: .5px;
    text-transform: uppercase;
    color: var(--brand-blue);
  }
  .divider {
    width: 1px;
    height: 110px;
    background: linear-gradient(to bottom, transparent, var(--divider), transparent);
  }
  .contact-block {
    padding-left: 28px;
    display: flex;
    flex-direction: column;
  }
  .person-name {
    font-weight: 700;
    font-size: 16px;
    text-transform: uppercase;
    color: var(--brand-blue);
  }
  .person-title {
    font-size: 16px;
    text-transform: uppercase;
    color: var(--accent-green);
    margin-bottom: 12px;
  }
  .contact-line {
    display: flex;
    align-items: center;
    gap: 8px;
    font-size: 15px;
    color: var(--text-light);
    line-height: 1.4;
  }
  .contact-line svg { width: 12px; height: 12px; fill: var(--text-light); flex: none; }
</style>
</head>
<body>
  <section class="card card-back" aria-label="Card back">
    <div class="brand-disc"></div>
    <div class="brand-name-large">Keston Fieldworks</div>
    <div class="social-row">
      <span class="social-dot"></span>
      <span class="social-dot"></span>
      <span class="social-dot"></span>
    </div>
  </section>

  <section class="card card-front" aria-label="Card front">
    <div class="brand-block">
      <div class="brand-dot"></div>
      <div class="brand-name">Keston Fieldworks</div>
    </div>
    <div class="divider"></div>
    <div class="contact-block">
      <div class="person-name">Dean Harlow</div>
      <div class="person-title">Director</div>
      <div class="contact-line">
        <svg viewBox="0 0 12 12"><path d="M1 3c0-1 1-2 2-2l1.5 2.5-1 1c.5 1.3 1.7 2.5 3 3l1-1L11 8c0 1-1 2-2 2C5 10 1 7 1 3z"/></svg>
        <span>0487305526</span>
      </div>
      <div class="contact-line">
        <svg viewBox="0 0 12 12"><path d="M0 2h12v8H0z M0 2l6 4 6-4" fill="none" stroke="#f2f2f2" stroke-width="1.2"/></svg>
        <span>dean@kolvat.biz</span>
      </div>
      <div class="contact-line">
        <svg viewBox="0 0 12 12"><circle cx="6" cy="6" r="5" fill="none" stroke="#f2f2f2" stroke-width="1.2"/><path d="M1 6h10M6 1c-2.5 3-2.5 7 0 10M6 1c2.5 3 2.5 7 0 10" fill="none" stroke="#f2f2f2" stroke-width="1"/></svg>
        <span>www.kestonfieldworks.com</span>
      </div>
    </div>
  </section>
</body>
</html>
```